Real Estate Business Card

On the front side I want to have my info, my brokerage info.
On the back side I want have my complany’s logo, website and Facebook link. I will provide all this once I select a design.

I would like to see Black background and gold text, Dark Blue and gold text and White and blue text designs

Font styles to use
Sans Serif
Script

```html
<!DOCTYPE html>
<html lang="en">
<head>
<meta charset="utf-8">
<title>Northvale Real Estate – Business Card</title>
<link href="https://fonts.googleapis.com/css2?family=Montserrat:wght@600;800&family=Roboto:wght@400;500;700&display=swap" rel="stylesheet">
<style>
  :root {
    --backdrop: #d9d9db;
    --card: #1f1f20;
    --brand-red: #b3272b;
    --slate: #5c5f66;
    --muted: #7b7e84;
    --gold: #e3b93a;
    --ink-light: #f2f2f2;
    --rule: #8a8a8a;
  }
  * { box-sizing: border-box; margin: 0; padding: 0; }
  html, body {
    width: 1200px; height: 900px; overflow: hidden;
    background: var(--backdrop);
  }
  .canvas {
    position: relative; width: 1200px; height: 900px;
  }
  .card {
    position: absolute;
    width: 640px; height: 366px;
    background: var(--card);
    box-shadow: 0 6px 18px rgba(0,0,0,.18);
  }
  .card--front { left: 340px; top: 48px; }
  .card--back  { left: 220px; top: 486px; }

  /* front */
  .social-square {
    position: absolute; right: 22px; top: 20px;
    width: 16px; height: 16px; background: var(--gold); border-radius: 2px;
  }
  .brand {
    position: absolute; left: 0; right: 0; top: 128px;
    display: flex; flex-direction: column; align-items: center;
  }
  .brand__row { display: flex; align-items: center; gap: 14px; }
  .brand__mark { width: 34px; height: 34px; background: var(--brand-red); }
  .brand__name {
    font-family: "Montserrat", sans-serif; font-weight: 800;
    font-size: 54px; letter-spacing: 1px; color: var(--slate); line-height: 1;
  }
  .brand__tag {
    margin-top: 10px;
    font-family: "Montserrat", sans-serif; font-weight: 600;
    font-size: 15px; letter-spacing: 9px; color: var(--muted);
  }

  /* back */
  .contact {
    position: absolute; left: 0; right: 0; top: 92px;
    display: flex; flex-direction: column; align-items: center;
    font-family: "Roboto", sans-serif; color: var(--ink-light); text-align: center;
  }
  .contact__mark { width: 52px; height: 46px; background: var(--gold); margin-bottom: 12px; }
  .contact__name { font-weight: 700; font-size: 22px; letter-spacing: .5px; }
  .contact__title { font-weight: 500; font-size: 16px; margin-top: 2px; }
  .contact__rule { width: 120px; height: 1px; background: var(--rule); margin: 12px 0 10px; }
  .contact__line { font-size: 15px; line-height: 1.5; }
</style>
</head>
<body>
<main class="canvas">
  <section class="card card--front" aria-label="Card front">
    <span class="social-square"></span>
    <div class="brand">
      <div class="brand__row">
        <span class="brand__mark"></span>
        <span class="brand__name">NORTHVALE</span>
      </div>
      <span class="brand__tag">REAL ESTATE</span>
    </div>
  </section>

  <section class="card card--back" aria-label="Card back">
    <div class="contact">
      <span class="contact__mark"></span>
      <p class="contact__name">DANIEL HALE</p>
      <p class="contact__title">CEO/FOUNDER</p>
      <span class="contact__rule"></span>
      <p class="contact__line">P. 555 201 4830 C. 555 376 9012</p>
      <p class="contact__line">E. daniel@northvale.com FB/northvale</p>
      <p class="contact__line">www.northvale.com</p>
    </div>
  </section>
</main>
</body>
</html>
```